Harbor Seal Works Spray Foam Appications website

We need a custom website for our company, www.harborsealworks.example. We need something we can modify by adding/changing content, photos, updated projects, etc. We are a commercial contractor specializing in Spray Foam applications. We want the website to be very creative and easy to navigate. The main points of the website are to showcase our projects, and describe our scope of services. We provide spray foam applications to the residential and commercial market. We offer Spray Foam roofing applications, as well as Spray Foam interior insulation applications. We also provide Roof Restoration Coating Systems to refurbish old and failing metal roofs. We would be ok with a one page web design if we can get the scope of our services to flow in a single page. The designer can decide if single or multiple pages works best for our business. One of the suppliers we work with is www.verdansupply.example.

Target Market(s)

Residential Home Builders, General Contractors, Commercial Construction Companies, Property Management Groups.

Industry/Entity Type

Insulation

Number of Pages Required

5+ page

Font styles to use
Serif
Sans Serif

Colors

Designer to choose colors to be used in the design.

Requirements
Must have
• We already have a Wix page, so website must be a Wix theme design. Nice easy to navigate format. Color matched to our current logo theme. We already have brochures and would like for it to match what's already in the hands of some of our customers. Need to be able to manage content to update photos, projects, scope of service, etc., via Wix. Current hold/splash page is hosted at www.harborsealworks.example. We would also like to have this video posted on the home page: https://www.videohost.example/watch?v=QxT4pLm9ZrA&feature=share
Nice to have
• I have attached some splash videos, being able to incorporate these somehow without being overpowering would be nice.

```html
<!DOCTYPE html>
<html lang="en">
<head>
<meta charset="utf-8">
<title>Harbor Seal Works</title>
<link href="https://fonts.googleapis.com/css2?family=Montserrat:wght@500;700&family=Poppins:wght@400;500;600;700&display=swap" rel="stylesheet">
<style>
:root{
  --orange:#f0a419;
  --ink:#1a1a1a;
  --white:#ffffff;
  --grey:#ececec;
  --night:#000000;
  --hero-a:#3a2c12;
  --hero-b:#20180c;
}
*{margin:0;padding:0;box-sizing:border-box}
html,body{width:1200px;height:2969px;overflow:hidden;background:var(--white)}
body{font-family:"Poppins",sans-serif;color:var(--ink)}
.page{position:relative;width:1200px;height:2969px;overflow:hidden}
.abs{position:absolute}

/* hero */
.hero{left:0;top:0;width:1200px;height:628px;background:radial-gradient(ellipse at 40% 35%,#4a4418 0%,var(--hero-a) 40%,var(--hero-b) 100%)}
.brand{left:82px;top:22px;display:flex;align-items:center;gap:14px}
.brand-dot{width:98px;height:98px;border-radius:50%;border:5px solid var(--orange)}
.brand-name{font-family:"Poppins",sans-serif;font-weight:600;font-size:30px;color:var(--orange);letter-spacing:1px}
.nav{top:58px;left:552px;display:flex;gap:0;font-size:17px;color:var(--white)}
.nav a{color:var(--white);text-decoration:none;position:absolute;white-space:nowrap}
.nav a.active{color:var(--orange)}
.book-online{left:964px;top:56px;width:164px;height:30px;background:var(--orange);color:var(--ink);font-size:17px;display:flex;align-items:center;justify-content:center}
.hero-title{left:0;width:1200px;top:318px;text-align:center;font-family:"Montserrat",sans-serif;font-weight:700;font-size:72px;color:var(--white);line-height:1}
.hero-sub{left:0;width:1200px;top:405px;text-align:center;font-family:"Montserrat",sans-serif;font-weight:500;font-size:38px;letter-spacing:9px;color:var(--white)}
.social span{position:absolute;width:11px;height:11px;border-radius:50%;background:var(--white)}

/* services */
.section-title{font-family:"Poppins",sans-serif;font-weight:700;font-size:35px;color:var(--ink)}
.services-title{left:0;width:1200px;top:692px;text-align:center}
.service{width:340px;text-align:center}
.service-icon{width:180px;height:160px;margin:0 auto;background:linear-gradient(#f3f3f3,#e3e3e3);border-radius:8px}
.service h3{font-weight:500;font-size:28px;margin-top:32px;line-height:1.3}
.service p{font-size:13.5px;font-weight:500;line-height:22.3px;margin-top:16px}
.book-now{left:538px;top:1217px;width:124px;height:35px;background:var(--orange);font-size:16px;display:flex;align-items:center;justify-content:center}

/* story */
.story-panel{left:0;top:1416px;width:1200px;height:573px;background:var(--grey)}
.story-video{left:0;top:1329px;width:598px;height:551px;background:linear-gradient(100deg,#7a5a33 0%,#b88b55 35%,#9a8aa8 55%,#c9a476 80%,#6e4a2c 100%)}
.play{left:230px;top:1541px;width:117px;height:117px;border-radius:50%;background:rgba(30,30,30,.88)}
.story-title{left:638px;top:1474px}
.story-text{left:646px;top:1540px;width:480px;font-size:13.5px;font-weight:500;line-height:22.3px}
.story-text p+p{margin-top:29px}

/* projects */
.dark{left:0;top:1989px;width:1200px;height:980px;background:linear-gradient(#3a3835 0%,#2c2b2a 30%,#1f1e1d 100%)}
.projects-title{left:0;width:1200px;top:2040px;text-align:center;font-weight:700;font-size:38px;line-height:43px;color:var(--white)}
.project{top:2207px;width:239px;height:177px}
.p1{background:linear-gradient(#6f9ad1 0%,#c9b99a 45%,#d6b24b 100%)}
.p2{background:linear-gradient(#6e95c8 0%,#9aa0a3 35%,#bfc2c4 100%)}
.p3{background:linear-gradient(#8a8f94 0%,#c4c6c8 30%,#e8eaeb 100%)}
.p4{background:linear-gradient(#9aa3ad 0%,#c9ccd0 35%,#eef0f1 100%)}

/* info */
.box{left:75px;width:1049px;background:var(--night);border:1px solid var(--orange)}
.hours{top:2456px;height:214px}
.visit{top:2672px;height:216px}
.box-title{font-family:"Montserrat",sans-serif;font-weight:500;font-size:25px;letter-spacing:2.5px;color:var(--orange);text-align:center}
.col{width:320px;text-align:center;color:var(--white)}
.col .day{font-size:16px}
.col .time{font-size:24px;margin-top:10px}
.visit-text{color:var(--white);font-size:16px;text-align:center;width:500px}
.form{left:696px;top:2733px;width:360px;color:var(--white);font-size:13.5px;font-weight:500}
.field{position:absolute;border:1px solid var(--white);padding:9px 16px;height:35px}
.submit{position:absolute;left:0;top:70px;width:360px;height:36px;background:var(--orange);color:var(--night);font-weight:700;display:flex;align-items:center;justify-content:center}
.chat{left:1129px;top:2833px;width:56px;height:56px;border-radius:50%;background:var(--orange);border:2px solid var(--white)}
.copyright{left:0;width:1200px;top:2905px;text-align:center;color:var(--orange);font-size:14px}
</style>
</head>
<body>
<div class="page">

  <div class="abs hero" role="img" aria-label="Dark smoky background with swirling olive and amber foam texture"></div>
  <div class="abs brand">
    <span class="brand-dot"></span>
    <span class="brand-name">HARBOR SEAL WORKS</span>
  </div>
  <nav class="abs nav">
    <a class="active" style="left:0">Service</a>
    <a style="left:99px">About Us</a>
    <a style="left:211px">Projects</a>
    <a style="left:315px">Contact</a>
  </nav>
  <div class="abs book-online">Book Online</div>
  <h1 class="abs hero-title">HARBOR SEAL</h1>
  <div class="abs hero-sub">WORKS</div>
  <div class="social">
    <span style="left:548px;top:491px"></span>
    <span style="left:590px;top:491px"></span>
    <span style="left:638px;top:491px"></span>
  </div>

  <h2 class="abs section-title services-title">OUR SERVICES</h2>
  <div class="abs service" style="left:64px;top:795px">
    <div class="service-icon" role="img" aria-label="Line illustration of stacked roof tiles"></div>
    <h3>Interior foam insulation</h3>
    <p>improve energy efficiency - up to 45% energy savings, Maintain consistent temperatures, Increase racking strength, Firm adherence to framing members and substrates ,Reduce HAVC size, FEMA- approved , flood - resistant insulation material</p>
  </div>
  <div class="abs service" style="left:430px;top:795px">
    <div class="service-icon" role="img" aria-label="Line illustration of a circle filled with scalloped roof shingles"></div>
    <h3>Foam Roof Application</h3>
    <p>Lifetime maintainable system, seamless self - adhering system, weather durability,, Energy conservation, zero thermal bridging<br>Fire retardant</p>
  </div>
  <div class="abs service" style="left:791px;top:795px">
    <div class="service-icon" role="img" aria-label="Line illustration of a house with a tiled roof surrounded by stars"></div>
    <h3>Roof Restoration</h3>
    <p>Repair without replacing - eliminates tear off, Warranties available, Preserve, protect , and prolong roof life, UV light resistant - cooler roof - cooler interior , Energy savings</p>
  </div>
  <div class="abs book-now">Book Now</div>

  <div class="abs story-panel"></div>
  <div class="abs story-video" role="img" aria-label="Video still of a gloved hand spraying foam insulation into a wall frame beside a window"></div>
  <svg class="abs play" viewBox="0 0 117 117" aria-hidden="true"><polygon points="50,38 50,80 78,59" fill="#fff"/></svg>
  <h2 class="abs section-title story-title">OUR STORY</h2>
  <div class="abs story-text">
    <p>Sed ut perspiciatis unde omnis iste natus error sit voluptatem accusantium doloremque laudantium, totam rem aperiam, eaque ipsa quae ab illo inventore veritatis et quasi architecto beatae vitae dicta sunt explicabo. Nemo enim ipsam voluptatem quia voluptas sit aspernatur aut odit aut fugit, sed quia consequuntur magni dolores eos qui ratione voluptatem sequi nesciunt.</p>
    <p>Neque porro quisquam est, qui dolorem ipsum quia dolor sit amet, consectetur, adipisci velit, sed quia non numquam eius modi tempora incidunt ut labore et dolore magnam aliquam quaerat voluptatem</p>
  </div>

  <div class="abs dark" role="img" aria-label="Dim warehouse interior with corrugated metal walls"></div>
  <h2 class="abs projects-title">We work with the best<br>Projects in the world</h2>
  <div class="abs project p1" style="left:75px" role="img" aria-label="Building with fresh yellow spray foam roof"></div>
  <div class="abs project p2" style="left:346px" role="img" aria-label="Grey corrugated metal roof before coating"></div>
  <div class="abs project p3" style="left:615px" role="img" aria-label="Worker on a white coated metal roof"></div>
  <div class="abs project p4" style="left:885px" role="img" aria-label="Finished white restored metal roof"></div>

  <div class="abs box hours">
    <div class="box-title" style="margin-top:40px">Working Hours</div>
  </div>
  <div class="abs col" style="left:78px;top:2566px"><div class="day">Sunday - Monday</div><div class="time">Closed</div></div>
  <div class="abs col" style="left:440px;top:2566px"><div class="day">Tuesday - Friday</div><div class="time">10:00am - 7:00pm</div></div>
  <div class="abs col" style="left:782px;top:2566px"><div class="day">Saturday</div><div class="time">11:00am - 5:00pm</div></div>

  <div class="abs box visit"></div>
  <div class="abs box-title" style="left:146px;width:400px;top:2692px">Visit Us</div>
  <div class="abs visit-text" style="left:96px;top:2752px">214 Pier Lane Bayview, CA 90417</div>
  <div class="abs visit-text" style="left:96px;top:2788px">info@harborsealworks.example &nbsp;&nbsp; 555-014-2290</div>
  <div class="social">
    <span style="left:292px;top:2841px"></span>
    <span style="left:334px;top:2841px"></span>
    <span style="left:382px;top:2841px"></span>
  </div>
  <div class="abs box-title" style="left:645px;width:400px;top:2692px">Contact Us</div>
  <div class="abs form">
    <div class="field" style="left:0;top:0;width:164px">First name</div>
    <div class="field" style="left:163px;top:0;width:197px;padding-left:44px">Email</div>
    <div class="field" style="left:0;top:34px;width:360px">Type your Message here.....</div>
    <div class="submit">Submit</div>
  </div>
  <div class="abs chat"></div>
  <div class="abs copyright">copyright © 2020 &nbsp;| &nbsp;www.harborsealworks.example</div>

</div>
</body>
</html>
```